wealth management firm, professional group, new model

we have a logo that works but we need a card, white background using our colors...clean look

our tag line if can be used in

The Path From Saver to Steward

```html
<!DOCTYPE html>
<html lang="en">
<head>
<meta charset="utf-8">
<title>Velmore Wealth Partners – Business Card</title>
<link rel="stylesheet" href="https://fonts.googleapis.com/css2?family=Montserrat:wght@400;500;600&display=swap">
<style>
  :root {
    --backdrop: #e9e9e8;
    --paper: #f7f7f4;
    --navy: #1b2d52;
    --navy-ink: #2a3b5e;
    --navy-raised: #304674;
    --ink-grey: #4b505b;
    --on-navy: #e8ecf3;
  }
  * { box-sizing: border-box; margin: 0; padding: 0; }
  html, body {
    width: 1200px; height: 800px; overflow: hidden;
    background: var(--backdrop);
    font-family: "Montserrat", sans-serif;
  }
  .card {
    position: absolute;
    left: 405px;
    width: 400px;
    height: 260px;
  }
  .card--front { top: 113px; background: var(--paper); color: var(--navy-ink); }
  .card--back  { top: 438px; background: var(--navy); }

  /* Front */
  .front-brand {
    position: absolute;
    left: 18px; top: 68px;
    width: 200px;
    text-align: center;
    color: var(--navy-ink);
    font-weight: 400;
  }
  .front-brand__name { font-size: 23px; letter-spacing: 11px; margin-right: -11px; line-height: 1; white-space: nowrap; }
  .front-brand__sub  { font-size: 9.5px; letter-spacing: 2.4px; margin-top: 16px; white-space: nowrap; }

  .contact {
    position: absolute;
    right: 41px; top: 120px;
    text-align: right;
  }
  .contact__name  { font-size: 14px; font-weight: 600; color: var(--navy-ink); line-height: 1.1; }
  .contact__role  { font-size: 12px; color: var(--ink-grey); margin-top: 1px; letter-spacing: 0.3px; }
  .contact__mark  { display: inline-block; width: 6px; height: 6px; background: var(--navy-ink); margin-top: 11px; }
  .contact__lines { font-size: 10px; color: var(--ink-grey); line-height: 15.5px; margin-top: 8px; }
  .contact__line  { display: flex; justify-content: flex-end; align-items: center; gap: 5px; white-space: nowrap; }
  .contact__icon  { width: 10px; height: 8px; flex: none; }
  .contact__gap   { width: 4px; }

  /* Back */
  .back-brand {
    position: absolute;
    left: 0; right: 0; top: 118px;
    text-align: center;
    color: var(--navy-raised);
    font-weight: 400;
  }
  .back-brand__name { font-size: 34px; letter-spacing: 26px; margin-right: -26px; line-height: 1; white-space: nowrap; }
  .back-brand__sub  { font-size: 13px; letter-spacing: 4px; margin-top: 25px; white-space: nowrap; }
  .tagline {
    position: absolute;
    left: 0; right: 0; top: 218px;
    text-align: center;
    color: var(--on-navy);
    font-size: 9px;
    font-weight: 500;
    letter-spacing: 1.8px;
    white-space: nowrap;
  }
</style>
</head>
<body>

<section class="card card--front" aria-label="Card front">
  <div class="front-brand">
    <div class="front-brand__name">VELMORE</div>
    <div class="front-brand__sub">WEALTH PARTNERS</div>
  </div>

  <div class="contact">
    <div class="contact__name">DANIEL R. HALE</div>
    <div class="contact__role">Brand Manager</div>
    <span class="contact__mark"></span>
    <div class="contact__lines">
      <div class="contact__line">Piazza Aurelia 5 2410 Milano, USA</div>
      <div class="contact__line">
        info@velmoremail.com
        <svg class="contact__icon" viewBox="0 0 10 8" aria-hidden="true"><rect x="0.5" y="0.5" width="9" height="7" fill="none" stroke="#2a3b5e"/><path d="M0.5 0.5 L5 4.5 L9.5 0.5 M0.5 7.5 L4 3.6 M9.5 7.5 L6 3.6" fill="none" stroke="#2a3b5e" stroke-width="0.8"/></svg>
        <span class="contact__gap"></span>
        +39.340.555.0182
        <svg class="contact__icon" viewBox="0 0 10 9" aria-hidden="true"><path d="M0.5 3 C0.5 0.5 9.5 0.5 9.5 3 L7.5 3.6 L7 2.4 C5.5 2 4.5 2 3 2.4 L2.5 3.6 Z" fill="#2a3b5e"/><path d="M2.3 4 L7.7 4 L9 8.5 L1 8.5 Z" fill="#2a3b5e"/><circle cx="5" cy="6.2" r="1.1" fill="#f7f7f4"/></svg>
      </div>
      <div class="contact__line">www.velmoreweb.com</div>
    </div>
  </div>
</section>

<section class="card card--back" aria-label="Card back">
  <div class="back-brand">
    <div class="back-brand__name">VELMORE</div>
    <div class="back-brand__sub">WEALTH PARTNERS</div>
  </div>
  <p class="tagline">THE PATH FROM SAVER TO STEWARD</p>
</section>

</body>
</html>
```